New Business Card Design Project

We would like a business card that represents the sale of boat, home, auto, and life insurance.

The logo can change colors to meet the look of the design if needed.

Industry/Entity Type

Business

```html
<!DOCTYPE html>
<html lang="en">
<head>
<meta charset="utf-8">
<title>Alder Financial – Business Card</title>
<link href="https://fonts.googleapis.com/css2?family=Open+Sans:wght@300;400;600&display=swap" rel="stylesheet">
<style>
  :root {
    --backdrop: #e9e7e3;
    --card-white: #ffffff;
    --card-white-shade: #f0f0f0;
    --slate: #4a4d50;
    --slate-dark: #2f3235;
    --teal: #3f8fa5;
    --teal-dark: #2f7489;
    --ink-grey: #5e6164;
    --text-light: #f2f4f5;
  }
  * { box-sizing: border-box; margin: 0; padding: 0; }
  html, body {
    width: 1200px; height: 1023px; overflow: hidden;
    background: var(--backdrop);
    font-family: "Open Sans", Arial, sans-serif;
  }
  .canvas {
    width: 1200px; height: 1023px;
    display: flex; align-items: center; justify-content: center;
  }
  .card {
    position: relative;
    width: 1000px; height: 572px;
    border-radius: 26px;
    overflow: hidden;
    background: linear-gradient(180deg, var(--card-white) 0%, var(--card-white-shade) 100%);
    box-shadow: 0 18px 40px rgba(0,0,0,.18);
  }
  .brand-area {
    position: absolute; left: 0; top: 0; width: 100%; height: 300px;
    display: flex; align-items: center; justify-content: center;
  }
  .brand-mark {
    width: 30px; height: 30px; border-radius: 50%;
    background: var(--teal);
    margin-right: 18px;
    flex: none;
  }
  .brand-name {
    font-weight: 400; font-size: 48px;
    color: var(--ink-grey); line-height: 1;
  }
  .teal-rule {
    position: absolute; left: 0; top: 340px; width: 100%; height: 8px;
    background: var(--teal);
  }
  .contact-band {
    position: absolute; left: 0; top: 348px; width: 100%; height: 224px;
    background: linear-gradient(160deg, var(--slate) 0%, var(--slate-dark) 55%, var(--slate) 100%);
  }
  .contact-list {
    list-style: none;
    position: absolute; left: 56px; top: 20px;
    color: var(--text-light); font-size: 19px; font-weight: 400;
  }
  .contact-list li { display: flex; align-items: center; height: 30px; }
  .contact-list svg { width: 18px; height: 18px; margin-right: 18px; fill: var(--text-light); flex: none; }
  .name-tab {
    position: absolute; right: 0; top: 300px;
    width: 300px; height: 96px;
    background: linear-gradient(180deg, var(--teal) 0%, var(--teal-dark) 100%);
    color: var(--text-light);
    text-align: right; padding: 12px 28px 0 0;
  }
  .name-tab .person-name { font-size: 34px; font-weight: 400; line-height: 1.1; }
  .name-tab .person-role { font-size: 19px; font-weight: 300; }
</style>
</head>
<body>
<main class="canvas">
  <article class="card">
    <section class="brand-area">
      <div class="brand-mark"></div>
      <div class="brand-name">Alder Financial</div>
    </section>

    <div class="teal-rule"></div>

    <section class="contact-band">
      <ul class="contact-list">
        <li>
          <svg viewBox="0 0 24 24" aria-hidden="true"><path d="M12 2a7 7 0 0 0-7 7c0 5 7 13 7 13s7-8 7-13a7 7 0 0 0-7-7zm0 9.5A2.5 2.5 0 1 1 12 6.5a2.5 2.5 0 0 1 0 5z"/></svg>
          address street address
        </li>
        <li><svg viewBox="0 0 24 24" aria-hidden="true"></svg>suite number, city, state, zip</li>
        <li>
          <svg viewBox="0 0 24 24" aria-hidden="true"><path d="M6.6 10.8a15 15 0 0 0 6.6 6.6l2.2-2.2a1 1 0 0 1 1-.25 11.4 11.4 0 0 0 3.6.6 1 1 0 0 1 1 1V20a1 1 0 0 1-1 1A17 17 0 0 1 3 4a1 1 0 0 1 1-1h3.5a1 1 0 0 1 1 1c0 1.25.2 2.45.6 3.6a1 1 0 0 1-.25 1z"/></svg>
          0123 456 789
        </li>
        <li>
          <svg viewBox="0 0 24 24" aria-hidden="true"><path d="M7 2h10a2 2 0 0 1 2 2v16a2 2 0 0 1-2 2H7a2 2 0 0 1-2-2V4a2 2 0 0 1 2-2zm0 3v13h10V5z"/></svg>
          0123 456 789
        </li>
        <li>
          <svg viewBox="0 0 24 24" aria-hidden="true"><path d="M3 5h18v14H3zm2 2v.5l7 4.5 7-4.5V7zm0 2.8V17h14V9.8l-7 4.5z"/></svg>
          youremail@example.com
        </li>
        <li>
          <svg viewBox="0 0 24 24" aria-hidden="true"><path d="M12 2a10 10 0 1 0 0 20 10 10 0 0 0 0-20zm0 2c.9 0 2.2 1.8 2.7 5H9.3C9.8 5.8 11.1 4 12 4zM4.3 11h3c-.1.7-.1 1.3-.1 2H4.3a8 8 0 0 1 0-2zm.6 4h2.6c.3 1.5.8 2.9 1.4 3.8A8 8 0 0 1 4.9 15zm2.6-6H4.9a8 8 0 0 1 4-3.8C8.3 6.1 7.8 7.5 7.5 9zM12 20c-.9 0-2.2-1.8-2.7-5h5.4c-.5 3.2-1.8 5-2.7 5zm-2.9-7c0-.7 0-1.3.1-2h5.6c.1.7.1 1.3.1 2s0 1.3-.1 2H9.2c-.1-.7-.1-1.3-.1-2zm6 5.8c.6-.9 1.1-2.300 1.4-3.8h2.6a8 8 0 0 1-4 3.8zM16.8 13c0-.7 0-1.3-.1-2h3a8 8 0 0 1 0 2zm-.3-4c-.3-1.5-.8-2.9-1.400-3.8A8 8 0 0 1 19.1 9z"/></svg>
          www.yourwebsite.com
        </li>
      </ul>
    </section>

    <div class="name-tab">
      <div class="person-name">your name</div>
      <div class="person-role">designation</div>
    </div>
  </article>
</main>
</body>
</html>
```